RW Holloway LLC Business Card - Civil Engineering & Consulting Firm

We need a Business Card that is elegant, and masculine.  It is our Professional Civil Engineering & Consulting Company located in San Antonio TX (Not s construction or builder firm- no gears & no tool images please). We provide civil engineering services including  commercial site plans, grading and drainage plans, utility plans, hydraulics and hydrology, land planning, utility coordination, and other general civil engineering services related to commercial and residential development.
We have 2 existing Logos. We would like to convey reliability, strength, trustworthiness and attention to detail.  Blues and orange tones as per logo We are OK with the use of a darker blue in the mix.  We have 2 logo versions - Full Company Name Logo to go on the back of card, & Small Icon Logo for the front w/ personal Info.

Target Market(s)
Architects, Real Estate Developers, Other Strctural Engineers, Surveyers, General Contractors
Industry/Entity Type
Professional Civil Engineering
Contact Information for Business Card
Name, Position, Address, Cell & Office #, email, and company website
Font styles to use
Other font styles liked:
- Avian
Requirements
Should not have
- No Tools, No Gears, no Cranes, or Construction Equipment.

```html
<!DOCTYPE html>
<html lang="en">
<head>
<meta charset="utf-8">
<title>RW Holloway LLC – Business Card</title>
<link rel="stylesheet" href="https://fonts.googleapis.com/css2?family=Montserrat:wght@300;400;500;700&display=swap">
<style>
  :root {
    --stage: #8c8c8c;
    --card-light: #ebeaeb;
    --facet-white: #ffffff;
    --facet-grey: #d6d5d8;
    --orange: #ef8e2a;
    --ink: #1a1a1a;
    --blue: #79a8d0;
    --back-orange: #dc8b40;
    --white: #ffffff;
  }
  * { box-sizing: border-box; margin: 0; padding: 0; }
  html, body {
    width: 1160px; height: 1200px; overflow: hidden;
    background: var(--stage);
    font-family: "Montserrat", sans-serif;
  }
  .card {
    position: absolute; left: 199px; width: 777px; height: 441px;
    border-radius: 30px; overflow: hidden;
  }
  .card-front { top: 105px; background: var(--card-light); }
  .card-back {
    top: 633px;
    background: linear-gradient(170deg, var(--blue) 0%, #9aa3ac 42%, #c79f7c 70%, var(--back-orange) 100%);
  }
  .facets { position: absolute; inset: 0; width: 100%; height: 100%; }

  .brand-mark {
    position: absolute; left: 0; width: 777px; top: 108px;
    display: flex; justify-content: center; align-items: center; gap: 10px;
    color: var(--orange); font-weight: 700; font-size: 24px; letter-spacing: 0.5px;
  }
  .brand-mark .square { width: 14px; height: 14px; background: var(--orange); }

  .person { position: absolute; right: 433px; top: 286px; text-align: right; }
  .person-name { color: var(--orange); font-weight: 700; font-size: 26px; letter-spacing: 0.3px; line-height: 1; }
  .person-role { color: var(--ink); font-size: 20px; font-weight: 400; margin-top: 8px; line-height: 1; }

  .divider { position: absolute; left: 367px; top: 258px; width: 2px; height: 113px; background: var(--orange); }

  .contact-list { position: absolute; left: 392px; top: 256px; list-style: none; }
  .contact-list li {
    display: flex; align-items: center; height: 31px;
    color: var(--ink); font-size: 21px; font-weight: 400; line-height: 1;
  }
  .contact-list svg { width: 24px; height: 22px; margin-right: 14px; fill: var(--orange); }

  .address {
    position: absolute; left: 0; width: 777px; top: 394px; text-align: center;
    color: var(--ink); font-size: 21px; font-weight: 400; line-height: 1;
  }

  .company-name {
    position: absolute; left: 0; width: 777px; top: 170px; text-align: center;
    color: var(--white); font-weight: 300; font-size: 60px; letter-spacing: 4px; line-height: 1;
  }
</style>
</head>
<body>

<section class="card card-front">
  <svg class="facets" viewBox="0 0 777 441" preserveAspectRatio="none" aria-hidden="true">
    <polygon points="0,0 250,0 0,60" fill="var(--facet-grey)" opacity="0.5"/>
    <polygon points="250,0 410,0 410,441 120,441" fill="var(--facet-white)" opacity="0.45"/>
    <polygon points="0,190 410,240 410,441 0,441" fill="var(--facet-white)" opacity="0.3"/>
    <polygon points="0,60 75,210 0,190" fill="var(--facet-grey)" opacity="0.5"/>
    <polygon points="230,55 600,441 410,441" fill="var(--facet-white)" opacity="0.35"/>
    <polygon points="777,120 777,441 650,441 560,340" fill="var(--facet-grey)" opacity="0.35"/>
  </svg>

  <div class="brand-mark"><span class="square"></span>RW Holloway LLC</div>

  <div class="person">
    <p class="person-name">DANE WHITFIELD</p>
    <p class="person-role">Co-Founder</p>
  </div>

  <div class="divider"></div>

  <ul class="contact-list">
    <li>
      <svg viewBox="0 0 24 24" aria-hidden="true"><path d="M6.6 10.8a15 15 0 0 0 6.6 6.6l2.2-2.2c.3-.3.7-.4 1-.2 1.1.4 2.3.6 3.6.6.6 0 1 .4 1 1V20c0 .6-.4 1-1 1A17 17 0 0 1 3 4c0-.6.4-1 1-1h3.5c.6 0 1 .4 1 1 0 1.3.2 2.5.6 3.6.1.3 0 .7-.2 1z"/></svg>
      555-014-0209
    </li>
    <li>
      <svg viewBox="0 0 24 24" aria-hidden="true"><path d="M2 8c2-3 18-3 20 0v2h-5V8H7v2H2zM6 11h12l3 9H3z"/></svg>
      555-014-0307
    </li>
    <li>
      <svg viewBox="0 0 24 24" aria-hidden="true"><path d="M2 5h20v2l-10 6L2 7zM2 9l10 6 10-6v10H2z"/></svg>
      info@rwhollowayllc
    </li>
    <li>
      <svg viewBox="0 0 24 24" aria-hidden="true"><circle cx="12" cy="12" r="10"/></svg>
      www.rwhollowayeng.com
    </li>
  </ul>

  <p class="address">4180 N. Ridge Road Suite 210 Alamo Vista 28</p>
</section>

<section class="card card-back">
  <svg class="facets" viewBox="0 0 777 441" preserveAspectRatio="none" aria-hidden="true">
    <polygon points="0,30 140,441 90,441 0,170" fill="var(--white)" opacity="0.08"/>
    <polygon points="210,0 390,0 390,441 180,441" fill="var(--white)" opacity="0.07"/>
    <polygon points="0,150 390,240 390,441 0,441" fill="var(--white)" opacity="0.06"/>
    <polygon points="390,0 777,0 777,70 620,441 390,441" fill="#000000" opacity="0.03"/>
    <polygon points="420,320 620,441 777,441 777,300" fill="var(--white)" opacity="0.06"/>
  </svg>

  <p class="company-name">RW HOLLOWAY LLC</p>
</section>

</body>
</html>
```